Website for a company offering full serivce charging solutions for electric cars

The company "tanu-werk" (english: "tanu-works") offering all-in-one-solutions for charging infrastructure for electric mobility.

There are four products:
1- Wallboxes for single-family homes
2- Solutions for property devloper/-management for property parking space
3- All-in-one-charging solution for municipalities/communities
4- Solutions for tourism/hotels/holiday appartments

The Website structure:
1. Main Page
2.1. Product Page Single Homes
2.2. Product Page Property Management / Parking
2.3. Product Page Municipality
2.4. Product Page Tourism
3. Contact Form / Request for information
4. Imprint / Legal

The Website should be built on Wordpress with a powerful possibility to simply add/modify specific landing pages.

We would like you to implement the website later and also maintain it if possible, but we would be able to do minor modifications by ourselfs (for A/B-Testing)

The website should be clear and simple, easy to understand.
Target group is mainly B2C without deeper knowledge of that topic.

It should suggest, that we will provide a very simple way to get the charging infrastructure done.

We need a contact form, maybe we will use Hubspot later.

Attached you will find a draft of the main page and a landing page (for 2.2) - it is just the content, please ignore the design. We would love to let you create a suitable design.
Also you will find some drafts a bit different for the same story.

I added also a few stock photos, but they don't need to be used! If you have better ideas, you are welcome!

Industry/Entity Type

Charging/Electric mobility

Number of Pages Required

2 page

Font styles to use
Sans Serif

Requirements
Must have
• Based on Wordpress, and the designer should be able to implement it on Wordpress on a later step

```html
<!DOCTYPE html>
<html lang="de">
<head>
<meta charset="utf-8">
<title>tanu-werk – Ladeinfrastruktur für Elektromobilität</title>
<link href="https://fonts.googleapis.com/css2?family=Poppins:wght@400;500;600;700&family=Oswald:wght@600;700&family=Exo+2:wght@500;600&display=swap" rel="stylesheet">
<style>
:root{
  --accent:#8a2ecb;
  --accent-pink:#d63fa6;
  --ink:#1e2230;
  --text:#555a66;
  --muted:#8a8f9a;
  --panel:#f4f4f6;
  --white:#ffffff;
  --footer:#111827;
  --footer-line:#2a3242;
}
*{box-sizing:border-box;margin:0;padding:0}
html,body{width:1200px;height:3516px;overflow:hidden}
body{font-family:"Poppins",sans-serif;color:var(--text);background:var(--white);position:relative}
.brand{display:flex;align-items:center;gap:12px;font-family:"Poppins",sans-serif;font-weight:600;font-size:26px;color:var(--ink)}
.brand-dot{width:26px;height:26px;border-radius:50%;background:var(--accent)}
.btn{display:inline-flex;align-items:center;gap:12px;height:44px;padding:0 22px 0 6px;border-radius:22px;font-size:15px;font-weight:500}
.btn-icon{width:32px;height:32px;border-radius:50%;background:linear-gradient(135deg,var(--accent-pink),var(--accent));display:flex;align-items:center;justify-content:center}
.btn-solid{background:linear-gradient(90deg,var(--accent),var(--accent-pink));color:var(--white)}
.btn-solid .btn-icon{background:var(--white)}
.btn-outline{border:2px solid var(--ink);color:var(--ink)}

/* header + hero */
.hero{position:absolute;left:0;top:0;width:1200px;height:620px;overflow:hidden}
.hero-photo{position:absolute;inset:0;background:linear-gradient(100deg,#f6f7f9 0%,#eef1f4 45%,#c8d1da 70%,#8f9aa6 100%)}
.site-header{position:absolute;top:0;left:0;right:0;height:84px;display:flex;align-items:center;justify-content:space-between;padding:0 100px 0 160px}
.main-nav{display:flex;gap:36px;font-size:14px;color:var(--ink)}
.main-nav a{text-decoration:none;color:inherit}
.main-nav .active{border-bottom:2px solid var(--ink);padding-bottom:4px}
.hero-copy{position:absolute;left:160px;top:236px;width:560px}
.hero-title{font-family:"Oswald",sans-serif;font-weight:700;font-size:44px;line-height:1.1;color:var(--ink);text-transform:uppercase;margin-bottom:56px}

/* partner */
.partner{position:absolute;top:728px;left:0;width:1200px;height:460px}
.partner-photo{position:absolute;left:200px;top:0;width:400px;height:452px;background:linear-gradient(160deg,#f2b46a 0%,#d98a4c 40%,#6c4a3a 80%,#3a2c2a 100%);box-shadow:0 10px 30px rgba(0,0,0,.12)}
.partner-copy{position:absolute;left:640px;top:40px;width:420px;font-size:12.5px;line-height:1.65}
.section-title{font-family:"Exo 2",sans-serif;font-weight:600;color:var(--ink)}
.partner-copy h2{font-size:30px;margin-bottom:14px}
.partner-copy .lead{font-weight:600;color:var(--ink);margin-bottom:14px}
.partner-copy p{margin-bottom:14px}

.solutions-title{position:absolute;top:1296px;left:200px;width:800px;text-align:center;font-size:36px;line-height:1.3}

/* solution rows */
.solution{position:absolute;left:0;width:1200px;display:flex}
.solution-panel{width:600px;background:var(--panel);padding:0 70px 0 160px;display:flex;flex-direction:column;justify-content:center}
.solution-panel.right{padding:0 100px 0 70px}
.solution-photo{width:600px}
.solution h3{font-family:"Poppins",sans-serif;font-weight:500;font-size:22px;color:var(--accent);margin-bottom:18px}
.solution ul{list-style:none;font-size:12.5px;line-height:1.6;margin-bottom:22px}
.solution li{position:relative;padding-left:18px;margin-bottom:4px}
.solution li::before{content:"";position:absolute;left:0;top:8px;width:6px;height:6px;border-radius:50%;background:var(--accent)}
.solution li ul{margin:6px 0 4px}
.solution li li::before{background:var(--muted)}
.privat{top:1488px;height:492px}
.geschaeft{top:1980px;height:600px}
.kommune{top:2580px;height:580px}
.photo-house{background:linear-gradient(170deg,#eef2f6 0%,#dfe3e6 45%,#9ca68f 80%,#6f7a62 100%)}
.photo-office{background:linear-gradient(135deg,#c9c3b8 0%,#e7e2da 40%,#a9a399 75%,#7d776e 100%)}
.photo-hall{background:linear-gradient(175deg,#f1f3f5 0%,#dcd7cc 40%,#b29d82 75%,#5f6b4e 100%)}

/* footer */
.site-footer{position:absolute;top:3160px;left:0;width:1200px;height:356px;background:var(--footer);color:#c7ccd6;font-size:13px}
.footer-top{position:absolute;top:68px;left:160px;right:100px;display:flex;align-items:center}
.site-footer .brand{color:var(--white)}
.contact-item{display:flex;gap:12px;align-items:flex-start;line-height:1.5}
.contact-item strong{display:block;color:var(--white);font-weight:600}
.contact-ic{width:22px;height:22px;flex:none;margin-top:2px}
.footer-line{position:absolute;top:178px;left:160px;right:100px;height:1px;background:var(--footer-line)}
.footer-nav{position:absolute;top:212px;left:160px;right:100px;display:flex;justify-content:space-between;color:var(--white)}
.footer-nav .active{border-bottom:2px solid var(--white);padding-bottom:4px;font-weight:600}
.footer-bottom{position:absolute;top:280px;left:160px;right:100px;display:flex;justify-content:space-between;align-items:center;color:var(--muted)}
.social{display:flex;gap:14px}
.social span{width:26px;height:26px;border-radius:50%;border:1.5px solid #6b7385}
.social span:first-child{background:var(--accent-pink);border-color:var(--accent-pink)}
</style>
</head>
<body>

<section class="hero">
  <div class="hero-photo" role="img" aria-label="Elektroauto wird an einer Ladestation geladen, Ladekabel im Vordergrund"></div>
  <header class="site-header">
    <div class="brand"><span class="brand-dot"></span>tanu-werk.de</div>
    <nav class="main-nav">
      <a class="active">Startseite</a><a>Unternehmen</a><a>Dienstleistungen</a><a>Karriere</a><a>Kontakt</a>
    </nav>
  </header>
  <div class="hero-copy">
    <h1 class="hero-title">All-in-One-Lösungen für Ladeinfrastruktur für Elektromobilität anzubieten</h1>
    <a class="btn btn-solid"><span class="btn-icon"><svg width="14" height="14" viewBox="0 0 14 14"><path d="M2 7h9M7 3l4 4-4 4" stroke="#8a2ecb" stroke-width="2" fill="none"/></svg></span>Kontaktiere uns</a>
  </div>
</section>

<section class="partner">
  <div class="partner-photo" role="img" aria-label="Frau lädt ihr Elektroauto bei Sonnenuntergang"></div>
  <div class="partner-copy">
    <h2 class="section-title">Tanu-werk Ist Ihr Partner</h2>
    <p class="lead">Wenn das Laden nicht nur einfach, sondern die Umstellung auch aus einer Hand kommen soll.</p>
    <p>Wir bieten Lösungen speziell für Privatkunden, Geschäftskunden als auch Kommunen an. Sie erhalten bei uns eine Gesamtlösung aus einer Hand: Beratung, Planung, Installation und Wartung Ihrer Ladeinfrastruktur.</p>
    <p>Von der Beratung, über die Installation, Inbetriebnahme bis zur Abrechnung und Wartung übernehmen wir für Sie jeden Schritt. So können Sie sich auf das Wesentliche konzentrieren, während wir dafür sorgen, dass Ihr Fahrzeug jederzeit zuverlässig geladen ist.</p>
    <a class="btn btn-outline"><span class="btn-icon"><svg width="14" height="14" viewBox="0 0 14 14"><path d="M2 7h9M7 3l4 4-4 4" stroke="#fff" stroke-width="2" fill="none"/></svg></span>Weiterlesen</a>
  </div>
</section>

<h2 class="section-title solutions-title">Fragen Sie Uns Nach Der Auf Ihre Individuellen Bedürfnisse Zugeschnittenen Lösung</h2>

<section class="solution privat">
  <div class="solution-panel">
    <h3>Als Privatkunde</h3>
    <ul>
      <li>Bestandsanalyse mit umfangreicher Beratung über die Möglichkeiten der Umsetzung</li>
      <li>Planung und Übernahme der Anmeldung beim zuständigen Netzbetreiber</li>
      <li>Auswahl der passenden Wallbox, genau abgestimmt auf Ihr Fahrzeug und Ihre Bedürfnisse</li>
      <li>Installation aller notwendigen Materialien und Zubehör (Zählerschrank, Kabelwege etc.)</li>
      <li>Inbetriebnahme und Einweisung in die Ladetechnik</li>
    </ul>
    <a class="btn btn-outline"><span class="btn-icon"><svg width="14" height="14" viewBox="0 0 14 14"><path d="M2 7h9M7 3l4 4-4 4" stroke="#fff" stroke-width="2" fill="none"/></svg></span>Jetzt ansehen</a>
  </div>
  <div class="solution-photo photo-house" role="img" aria-label="Modernes Einfamilienhaus mit Einfahrt"></div>
</section>

<section class="solution geschaeft">
  <div class="solution-photo photo-office" role="img" aria-label="Team bei der Besprechung am Konferenztisch, Ansicht von oben"></div>
  <div class="solution-panel right">
    <h3>Als Geschäftskunde</h3>
    <ul>
      <li>Durchführung einer individuellen Bedarfsanalyse und Ermittlung der Anforderungen für:
        <ul>
          <li>Haus- und Immobilienverwaltungen</li>
          <li>Verwaltungen und Handelsunternehmen</li>
          <li>Hotel- und Beherbergungsbetriebe</li>
          <li>Parkraum- und Parkhausbetreiber</li>
          <li>Tourismus, Sport- und Freizeiteinrichtungen</li>
        </ul>
      </li>
      <li>Planung und Projektierung der Ladeinfrastruktur inklusive Lastmanagement</li>
      <li>Leasing oder Kauf der Ladesäulen</li>
    </ul>
    <a class="btn btn-outline"><span class="btn-icon"><svg width="14" height="14" viewBox="0 0 14 14"><path d="M2 7h9M7 3l4 4-4 4" stroke="#fff" stroke-width="2" fill="none"/></svg></span>Jetzt ansehen</a>
  </div>
</section>

<section class="solution kommune">
  <div class="solution-panel">
    <h3>Als Kommune</h3>
    <ul>
      <li>Konzepterstellung möglicher Ladeinfrastruktur-Standorte Ihrer Gemeinde</li>
      <li>Planung und Projektierung inkl. Ermittlung förderfähiger Maßnahmen</li>
      <li>Fördermittelberatung und Beantragung von Zuschüssen</li>
      <li>Fachgerechte Installation und Inbetriebnahme</li>
      <li>Regelmäßige Wartung, gemäß Vorschrift</li>
      <li>Reparatur und Kundenservice</li>
      <li>Direkte Abrechnung mit dem Nutzer</li>
    </ul>
    <a class="btn btn-outline"><span class="btn-icon"><svg width="14" height="14" viewBox="0 0 14 14"><path d="M2 7h9M7 3l4 4-4 4" stroke="#fff" stroke-width="2" fill="none"/></svg></span>Jetzt ansehen</a>
  </div>
  <div class="solution-photo photo-hall" role="img" aria-label="Historisches Rathausgebäude mit Vorplatz"></div>
</section>

<footer class="site-footer">
  <div class="footer-top">
    <div class="brand" style="width:360px"><span class="brand-dot"></span>tanu-werk.de</div>
    <div class="contact-item" style="width:300px">
      <svg class="contact-ic" viewBox="0 0 24 24"><path d="M12 2a7 7 0 0 0-7 7c0 5 7 13 7 13s7-8 7-13a7 7 0 0 0-7-7zm0 9.5A2.5 2.5 0 1 1 12 6.5a2.5 2.5 0 0 1 0 5z" fill="#d63fa6"/></svg>
      <span>Musterweg 12,<br>10115 Berlin</span>
    </div>
    <div class="contact-item" style="width:200px">
      <svg class="contact-ic" viewBox="0 0 24 24"><path d="M6.6 10.8a15 15 0 0 0 6.6 6.6l2.2-2.2a1 1 0 0 1 1-.25 11.4 11.4 0 0 0 3.6.57 1 1 0 0 1 1 1V20a1 1 0 0 1-1 1A17 17 0 0 1 3 4a1 1 0 0 1 1-1h3.5a1 1 0 0 1 1 1c0 1.25.2 2.45.57 3.57a1 1 0 0 1-.25 1z" fill="#d63fa6"/></svg>
      <span><strong>Telefon</strong>(01) 234 5678</span>
    </div>
    <div class="contact-item">
      <svg class="contact-ic" viewBox="0 0 24 24"><path d="M3 5h18v14H3z" fill="none" stroke="#d63fa6" stroke-width="2"/><path d="M3 6l9 7 9-7" fill="none" stroke="#d63fa6" stroke-width="2"/></svg>
      <span><strong>Email</strong>info@tanu-werk.de</span>
    </div>
  </div>
  <div class="footer-line"></div>
  <nav class="footer-nav">
    <a class="active">AGB</a><a>Datenschutzerklärung</a><a>FAQs</a><a>Karriere</a><a>Impressum</a><a>Kontakt</a>
  </nav>
  <div class="footer-bottom">
    <span>Copyright © 2020 tanu-werk GmbH. All Rights Reserved.</span>
    <div class="social"><span></span><span></span><span></span></div>
  </div>
</footer>

</body>
</html>
```